Maple Beacon Website

We are starting a marketing company and to do that we need a website! We want a website that will inspire and persuade to bring out the awesomeness in our clients.
What we want to see:
- Inspirational and persuasive imagery that relate to Branding.
- No cliche images eg. business man, suits and hand shakes
- We want to transform and educate our clients.
- We want to show them the path and would like our website to really act as a guide that guides them step by step through our process.
- We want the portray that we are an investment but not have a pretentious way to it. We put our heart into every project and that is how we treat our clients.
-When you submit your design please include what platform you have created for. Preference would be Wordpress or Joobla.

We have included the psd file for the wire frame, logo files, font files, site map and a link to a video we create to give you more information on what we would like to see. http://clipvault.example/t/qk82LmZpr

Feel free to make small modification to the logos if you think it will improve it. Your creativity and advice is most welcome.
Updates

One thing we forgot. We would like to have our contact information near the top of the website as well as at the bottom.  Here is out contact info:

Email: info@maplebeacon.example
Phone: 587-555-0142

Project Deadline Extended
Reason: As we are new with the platform and that we want to optimize our results, we decided to extend the deadline by 15 days. Thanks!

Target Market(s)

28-60, Male and Female, Oil field, Local Businesses, Dentists, Chiropractors, Hair salon, Construction/Renovation, Events etc

Industry/Entity Type

Investment

Requirements
Must have
• - 4 Inspirational and persuasive Imagery for the top portion of the website
- Must have a feel as if your not on a website an example of this is linked below.
http://www.artbidhub.example/design/402957/web-design-by-lena-torvik
Nice to have
• - Creative advice from you.
- Creative buttons for Get Free Quote and Subscribe buttons. Something out of the box that draws peoples attention. eg. a 'B' button. Just and example but still something related to branding.
Should not have
• No Cliches

```html
<!DOCTYPE html>
<html lang="en">
<head>
<meta charset="utf-8">
<title>Maple Beacon</title>
<link rel="stylesheet" href="https://fonts.googleapis.com/css2?family=Signika:wght@400;600;700&family=Arimo:wght@400;700&display=swap">
<style>
:root{
  --ink:#4a4f55;
  --ink-dark:#3a3d40;
  --steel:#4f6573;
  --steel-dark:#52606a;
  --lime:#8cbf3f;
  --grey-head:#a4a9ad;
  --side:#4a4a4a;
  --side-line:#3c3c3c;
  --white:#fff;
  --blue:#2f86c4;
  --blue-light:#4aa6e0;
  --cloud-a:#7a1f1f;
  --cloud-b:#e5b92e;
}
*{margin:0;padding:0;box-sizing:border-box}
html,body{width:1200px;height:712px;overflow:hidden}
body{position:relative;background:linear-gradient(#8b9ba4,#a7b4bb 60%,#b0bcc2);font-family:"Arimo",Arial,sans-serif;color:var(--ink)}
.header{position:absolute;left:0;top:0;width:1200px;height:86px;background:var(--white)}
.brand{position:absolute;left:208px;top:18px;display:flex;align-items:center;gap:8px}
.brand-dot{width:12px;height:12px;border-radius:50%;background:var(--lime)}
.brand-name{font-family:"Signika",sans-serif;font-weight:700;font-size:24px;color:#6d7176;letter-spacing:.3px}
.tagline{position:absolute;left:230px;top:64px;font-family:"Signika",sans-serif;font-style:italic;font-size:11px;color:#555}
.main-nav{position:absolute;top:38px;right:222px;display:flex;gap:19px;font-family:"Signika",sans-serif;font-weight:600;font-size:12px;color:var(--ink-dark);letter-spacing:.2px}
.sidebar{position:absolute;left:213px;top:106px;width:211px;height:276px;background:var(--side)}
.side-menu{list-style:none}
.side-menu li{height:33px;display:flex;align-items:center;padding-left:36px;position:relative;font-family:"Signika",sans-serif;font-weight:600;font-size:12px;color:#fff;border-bottom:2px solid var(--side-line)}
.side-menu li:first-child{height:43px;padding-top:10px}
.side-menu li:last-child{border-bottom:0}
.side-menu svg{position:absolute;left:15px;width:14px;height:14px}
.side-menu li:first-child svg{top:20px}
.connect-title{position:absolute;left:15px;top:210px;font-family:"Signika",sans-serif;font-weight:600;font-size:11.5px;color:#fff}
.social{position:absolute;left:16px;top:231px;display:flex;gap:3px}
.social span{width:24px;height:24px;border-radius:3px}
.slider{position:absolute;left:430px;top:106px;width:555px;height:276px;background:var(--steel)}
.slide{position:absolute;left:7px;top:7px;width:542px;height:263px;background:var(--white)}
.slide-art{position:absolute;left:8px;top:44px;width:526px;height:192px;border-radius:4px;background:radial-gradient(ellipse at 45% 55%,rgba(122,31,31,.55),transparent 55%),linear-gradient(100deg,#f2d98a,#e9c14d 35%,#b5473a 60%,#e8a030 85%,#f3d990)}
.slide-arrows{position:absolute;right:12px;bottom:10px}
.newsletter{position:absolute;left:211px;top:389px;width:774px;height:44px;background:var(--white)}
.news-title{position:absolute;left:19px;top:15px;font-family:"Signika",sans-serif;font-weight:600;font-size:11px;color:var(--steel)}
.news-text{position:absolute;left:202px;top:14px;font-size:12px;color:#444}
.news-input{position:absolute;left:479px;top:8px;width:228px;height:28px;border:1px solid #ccc;padding-left:14px;font-size:11px;color:#c4c4c4;line-height:26px}
.news-btn{position:absolute;left:711px;top:8px;width:56px;height:26px;background:#75868f;color:#fff;font-size:10px;line-height:26px;text-align:center}
.content{position:absolute;left:211px;top:442px;width:774px;height:144px;background:var(--white)}
.welcome{position:absolute;left:18px;top:9px;width:525px}
.section-title{font-family:"Signika",sans-serif;font-weight:700;font-size:13.5px;color:var(--grey-head)}
.section-title .dark{color:var(--steel)}
.section-title .lime{color:var(--lime)}
.welcome p{margin-top:12px;font-size:9.8px;line-height:15.2px;color:#444}
.read-more{font-family:"Signika",sans-serif;font-weight:600;font-size:10.5px;color:#444;margin-top:1px}
.divider{position:absolute;left:551px;top:8px;width:1px;height:128px;background:#ddd}
.quote{position:absolute;left:563px;top:9px;width:200px}
.quote p{margin-top:12px;font-size:9.8px;line-height:15.2px;color:#444}
.quote-btn{position:absolute;left:1px;top:89px}
.footer{position:absolute;left:210px;top:594px;width:774px;height:44px;background:var(--white)}
.footer-nav{position:absolute;left:20px;top:8px;font-family:"Signika",sans-serif;font-size:10.5px;color:#444;word-spacing:2px}
.footer-nav i{font-style:normal;margin:0 8px}
.copyright{position:absolute;left:21px;top:24px;font-family:"Signika",sans-serif;font-size:8.6px;color:#444;letter-spacing:.4px}
</style>
</head>
<body>
<header class="header">
  <div class="brand"><span class="brand-dot"></span><span class="brand-name">Maple Beacon</span></div>
  <div class="tagline">Because You're Awesome!</div>
  <nav class="main-nav"><span>MAPLE BEACON</span><span>BE FOUND</span><span>CONNECT</span><span>GET GROWING</span></nav>
</header>

<aside class="sidebar">
  <ul class="side-menu">
    <li><svg viewBox="0 0 14 14"><circle cx="7" cy="7" r="6.3" fill="none" stroke="#6a6a6a"/><path d="M5.5 4l3 3-3 3" fill="none" stroke="#7a7a7a" stroke-width="1.3"/></svg>STRATEGY</li>
    <li><svg viewBox="0 0 14 14"><circle cx="7" cy="7" r="6.3" fill="none" stroke="#6a6a6a"/><path d="M5.5 4l3 3-3 3" fill="none" stroke="#7a7a7a" stroke-width="1.3"/></svg>PORTFOLIO</li>
    <li><svg viewBox="0 0 14 14"><circle cx="7" cy="7" r="6.3" fill="none" stroke="#6a6a6a"/><path d="M5.5 4l3 3-3 3" fill="none" stroke="#7a7a7a" stroke-width="1.3"/></svg>ABOUT US</li>
    <li><svg viewBox="0 0 14 14"><circle cx="7" cy="7" r="6.3" fill="none" stroke="#6a6a6a"/><path d="M5.5 4l3 3-3 3" fill="none" stroke="#7a7a7a" stroke-width="1.3"/></svg>CONTACT US</li>
    <li><svg viewBox="0 0 14 14"><circle cx="7" cy="7" r="6.3" fill="none" stroke="#6a6a6a"/><path d="M5.5 4l3 3-3 3" fill="none" stroke="#7a7a7a" stroke-width="1.3"/></svg>BLOG</li>
  </ul>
  <div class="connect-title">CONNECT WITH US</div>
  <div class="social">
    <span style="background:#8fd3ef"></span>
    <span style="background:#86cde6"></span>
    <span style="background:#4a6eb0"></span>
    <span style="background:#f4f4f4"></span>
    <span style="background:#2f2f2f"></span>
  </div>
</aside>

<section class="slider">
  <div class="slide">
    <div class="slide-art" role="img" aria-label="Word cloud of branding and social media terms such as social media, monitoring, branding, online and tools"></div>
    <svg class="slide-arrows" width="34" height="14" viewBox="0 0 34 14"><path d="M13 0v14L0 7z" fill="#111"/><path d="M21 0v14l13-7z" fill="#111"/></svg>
  </div>
</section>

<section class="newsletter">
  <div class="news-title">GET TIPCS &amp; TRICKS EVERYDAY</div>
  <div class="news-text">Subscribe to our weekly newsletter for offers &amp; deals</div>
  <div class="news-input">enter your email here</div>
  <div class="news-btn">JOIN NOW</div>
</section>

<section class="content">
  <div class="welcome">
    <h2 class="section-title">WELCOME TO <span class="dark">MAPLE</span> <span class="lime">BEACON</span></h2>
    <p>Lorem ipsum dolor sit amet, consectetur adipisicing elit, sed do eiusmod tempor incididunt ut labore et dolore magna aliqua. Ut enim ad minim veniam, quis nostrud exercitation ullamco laboris nisi ut aliquip ex ea commodo consequat. Duis aute irur dolor in reprehenderit in voluptate velit esse cillum dolore eu fugiat nulla pariatur. Excepteur sint occaecat cupidatat non proident, sunt in culpa qui officia deserunt mollit anim id est laborum.</p>
    <div class="read-more">READ MORE..</div>
  </div>
  <div class="divider"></div>
  <div class="quote">
    <h2 class="section-title">GET A QUOTE</h2>
    <p>If you would like to have more information on how we can achieve your goals, you can visit our strategy page or simply get a free quote</p>
    <svg class="quote-btn" width="121" height="33" viewBox="0 0 121 33">
      <defs><linearGradient id="qb" x1="0" y1="0" x2="0" y2="1"><stop offset="0" stop-color="#56b3ea"/><stop offset="1" stop-color="#1f74b3"/></linearGradient></defs>
      <path d="M4 .5h104l12 16-12 16H4a3.5 3.5 0 0 1-3.5-3.5V4A3.5 3.5 0 0 1 4 .5z" fill="url(#qb)" stroke="#1a6aa6"/>
      <text x="10" y="21" font-family="Signika, sans-serif" font-weight="600" font-size="11" fill="#fff">GET A FREE QUOTE</text>
    </svg>
  </div>
</section>

<footer class="footer">
  <div class="footer-nav">SITEMAP<i>/</i>STRATEGY<i>/</i>PORTFOLIO<i>/</i>ABOUT US<i>/</i>CONTACT US<i>/</i>BLOG</div>
  <div class="copyright">COPYRIGHT 2013. ALL RIGHTS RESERVED. MAPLE BEACON INC.</div>
</footer>
</body>
</html>
```